Candle Rental Business seeks new website design

We need a new website design for a Candle hire business. The business rents out pillar candles for events such as weddings and corporate events. Our main target market is weddings. The business name is Hire a Lantern. The business name does not have a logo design.

We would like a website that is light in colours and creates a warm atmosphere. The design needs to be elegant and upmarket. There are different size candles that we hire out, ranging from 10cm diameter to 20cm diameter, flat, tall etc. All our candles are white in colour. Its just the size that differs.

We would also like to include a section for hiring out decor such as glassvases, candlebras, overlays and chairs sachets, chair covers. However, this is not the businesses main focus but an additional offering to customers.

Target Market(s)

Wedding venues and brides. Corporate events. School dances.

Industry/Entity Type

Hospitality

Logo Text

Hire a Lantern

Number of Pages Required

1 page

Font styles to use
Sans Serif
Script

Requirements
Must have
• Pictures of pillar candles. Plain white candles. The website must centre around candles.
Nice to have
• Different examples of candle centrepieces
Should not have
• Pictures must not be of brides. Pictures of surrounding is perferable.

```html
<!DOCTYPE html>
<html lang="en">
<head>
<meta charset="utf-8">
<title>Hire a Lantern</title>
<link rel="stylesheet" href="https://fonts.googleapis.com/css2?family=Righteous&family=Lato:wght@400;700&display=swap">
<style>
:root{
  --orange:#f7850f;
  --orange-deep:#e8760a;
  --black:#0b0b0b;
  --ink:#222;
  --grey-bg:#ececec;
  --line:#cfcfcf;
  --white:#fff;
}
*{box-sizing:border-box;margin:0;padding:0}
html,body{width:1200px;height:2284px;overflow:hidden}
body{position:relative;background:var(--white);font-family:"Lato",sans-serif;color:var(--ink)}
.abs{position:absolute}
.display{font-family:"Righteous",sans-serif}
.accent{color:var(--orange)}

/* header */
.site-header{left:0;top:0;width:1200px;height:136px}
.contact-strip{right:80px;top:30px;display:flex;gap:46px;font-size:19px;align-items:center}
.contact-strip span{display:flex;align-items:center;gap:12px}
.nav-bar{left:0;top:91px;width:1200px;height:45px;background:var(--orange)}
.brand-tab{left:36px;top:60px;width:232px;height:76px;background:var(--white);border-radius:0 0 30px 30px;display:flex;align-items:flex-end;justify-content:center;padding-bottom:10px;gap:8px}
.brand-name{font-family:"Righteous",sans-serif;font-size:19px;color:var(--orange);letter-spacing:.5px}
.brand-dot{width:12px;height:12px;border-radius:50%;background:var(--orange)}
.main-nav{left:305px;top:91px;height:45px;display:flex;list-style:none}
.main-nav li{width:180px;height:45px;display:flex;align-items:center;justify-content:center;color:var(--white);font-family:"Righteous",sans-serif;font-size:16px;border-right:1px solid rgba(255,255,255,.25)}
.main-nav li.active{width:100px;background:var(--black)}
.main-nav li:last-child{border-right:none}

/* hero */
.hero{left:0;top:136px;width:1200px;height:470px;background:radial-gradient(ellipse at 62% 40%,#f4d9a6 0%,#9a7fb8 25%,#5a4d8f 55%,#241c3a 100%)}
.hero-arrow{top:345px}
.hero-caption{left:80px;top:525px;width:1040px;height:54px;background:linear-gradient(90deg,rgba(232,118,10,.25),rgba(232,118,10,.75) 50%,rgba(232,118,10,.25));color:var(--white);font-family:"Righteous",sans-serif;font-size:31px;display:flex;align-items:center;justify-content:center;letter-spacing:.5px}

/* features */
.feature-strip{left:0;top:606px;width:1200px;height:107px;background:var(--black)}
.feature{top:635px;width:329px;height:50px;background:var(--white);display:flex;align-items:center;padding-left:92px;font-family:"Righteous",sans-serif;font-size:22px;color:var(--black)}
.feature-icon{top:628px;width:66px;height:66px;border-radius:50%;background:var(--orange);border:3px solid var(--black)}

/* welcome */
.welcome-photo{left:30px;top:807px;width:184px;height:176px;background:linear-gradient(180deg,#fafafa,#e4e4e4);border-radius:6px}
.welcome-mark{left:585px;top:750px;width:30px;height:30px;border-radius:50%;background:var(--orange)}
.welcome-title{left:0;top:810px;width:1200px;text-align:center;font-family:"Righteous",sans-serif;font-size:27px;color:var(--black)}
.welcome-text{left:118px;top:858px;width:966px;text-align:center;font-size:14.5px;line-height:23px}
.btn-dark{background:var(--black);color:var(--white);font-size:13px;font-weight:700;display:flex;align-items:center;justify-content:center}
.welcome-btn{left:555px;top:950px;width:90px;height:30px}

/* events */
.event{top:1019px;width:600px;height:399px;text-align:center;color:var(--white)}
.event-wedding{left:0;background:linear-gradient(180deg,#3a302a,#1c1613)}
.event-corporate{left:600px;background:linear-gradient(180deg,#f29a3c,#e8820f)}
.event-icon{position:absolute;left:262px;top:45px;width:76px;height:90px;border-radius:38px;background:rgba(255,255,255,.2)}
.event-corporate .event-icon{background:rgba(0,0,0,.15)}
.event-title{position:absolute;left:0;top:185px;width:600px;font-family:"Righteous",sans-serif;font-size:23px}
.event-corporate .event-title{color:var(--black)}
.event-text{position:absolute;left:155px;top:232px;width:290px;font-size:14px;line-height:21px}
.event-corporate .event-text{color:var(--ink)}
.event-btn{position:absolute;left:255px;top:316px;width:110px;height:36px;border:1px solid var(--white);display:flex;align-items:center;justify-content:center;font-size:14px}
.event-corporate .event-btn{border-color:var(--black);color:var(--black)}

/* testimonials */
.testimonial-title{left:0;top:1456px;width:1200px;text-align:center;font-family:"Righteous",sans-serif;font-size:27px;color:var(--black)}
.testimonial-rule{left:162px;top:1510px;width:876px;height:4px;border-top:1px solid var(--line);border-bottom:1px solid var(--line)}
.client-photo{left:113px;top:1543px;width:116px;height:116px;border-radius:50%;border:3px solid var(--orange);background:linear-gradient(180deg,#b5c3cc,#5d6a73)}
.quote-badge{left:210px;top:1573px;width:36px;height:36px;border-radius:50%;background:var(--black)}
.testimonial-text{left:270px;top:1550px;width:830px;font-size:14.5px;line-height:23.5px}
.client-name{left:270px;top:1658px;font-size:19px;font-weight:700}
.slider-dots{left:272px;top:1692px;display:flex;gap:4px}
.slider-dots i{width:9px;height:9px;border-radius:50%;background:#999}
.slider-dots i:first-child{background:var(--orange)}

/* decor + inquiry */
.lower{left:0;top:1744px;width:1200px;height:363px;background:var(--grey-bg)}
.section-title{font-family:"Righteous",sans-serif;font-size:24px;color:var(--black)}
.decor-title{left:81px;top:1774px}
.decor-rule{left:81px;top:1813px;width:514px;border-top:1px solid var(--line)}
.decor-intro{left:81px;top:1835px;font-size:16px}
.decor-list{left:81px;top:1886px;list-style:none;font-size:14px}
.decor-list li{height:36px;display:flex;gap:10px}
.decor-list li::before{content:"»";color:var(--orange);font-weight:700}
.decor-photo{left:445px;top:1890px;width:125px;height:165px;border-radius:10px;background:linear-gradient(180deg,#f6c26a 0,#fff4de 20%,#e6e6e6 40%,#c9c9c9 100%)}
.inquiry-title{left:668px;top:1774px}
.inquiry-rule{left:637px;top:1813px;width:483px;border-top:1px solid var(--line)}
.field{left:637px;width:483px;background:var(--white);border:1px solid #d6d6d6;font-size:13px;padding:10px 10px}
.submit{left:637px;top:2018px;width:106px;height:40px;font-size:17px;font-family:"Righteous",sans-serif}

/* footer */
.footer-nav{left:0;top:2107px;width:1200px;height:71px;background:var(--orange)}
.footer-links{left:81px;top:2132px;font-size:13px;color:var(--black);word-spacing:2px}
.footer-links span{margin:0 14px}
.social{top:2126px;width:33px;height:33px;border-radius:50%;background:var(--white)}
.footer{left:0;top:2178px;width:1200px;height:106px;background:var(--black);color:var(--white)}
.footer-item{top:2214px;display:flex;gap:12px;font-size:13px}
.footer-item b{display:block;font-size:15px;margin-bottom:5px}
.footer-pin{width:32px;height:32px;border-radius:50%;background:var(--orange);flex:none;display:flex;align-items:center;justify-content:center}
.footer-brand{left:855px;top:2205px;display:flex;align-items:center;gap:12px;font-family:"Righteous",sans-serif;font-size:20px}
.footer-brand i{width:14px;height:14px;border-radius:50%;background:#9a9a9a}
.copyright{left:800px;top:2250px;font-size:13px;color:#ddd}
</style>
</head>
<body>

<header class="abs site-header">
  <div class="abs contact-strip">
    <span><svg width="20" height="14" viewBox="0 0 20 14"><rect width="20" height="14" fill="#f7850f"/><path d="M0 0 L10 8 L20 0" stroke="#fff" stroke-width="1.6" fill="none"/></svg>info@hirealantern.com</span>
    <span><svg width="18" height="18" viewBox="0 0 24 24"><path d="M6.6 10.8a15 15 0 0 0 6.6 6.6l2.2-2.2c.3-.3.7-.4 1-.2 1.1.4 2.3.6 3.6.6.6 0 1 .4 1 1V20c0 .6-.4 1-1 1A17 17 0 0 1 3 4c0-.6.4-1 1-1h3.5c.6 0 1 .4 1 1 0 1.3.2 2.5.6 3.6.1.3 0 .7-.2 1z" fill="#f7850f"/></svg>123 456 7890</span>
  </div>
  <div class="abs nav-bar"></div>
  <div class="abs brand-tab"><i class="brand-dot"></i><span class="brand-name">HIRE A LANTERN</span></div>
  <ul class="abs main-nav">
    <li class="active">HOME</li>
    <li>ABOUT US</li>
    <li>OUR PRODUCTS</li>
    <li>TESTIMONIALS</li>
    <li>CONTACT US</li>
  </ul>
</header>

<section class="abs hero" role="img" aria-label="Candle-lit banquet table with floating pillar candles in tall glass vases"></section>
<svg class="abs hero-arrow" style="left:36px" width="28" height="52" viewBox="0 0 28 52"><path d="M26 2 L2 26 L26 50" stroke="#fff" stroke-width="2" fill="none" opacity=".8"/></svg>
<svg class="abs hero-arrow" style="left:1136px" width="28" height="52" viewBox="0 0 28 52"><path d="M2 2 L26 26 L2 50" stroke="#fff" stroke-width="2" fill="none" opacity=".8"/></svg>
<div class="abs hero-caption">WE DESIGN, MANUFACTURE &amp; PERSONALISE DECORATIVE CANDLES</div>

<section class="abs feature-strip"></section>
<div class="abs feature" style="left:81px">Hire Candles</div>
<div class="abs feature" style="left:436px">Personalised Candles</div>
<div class="abs feature" style="left:791px">Décor Hire</div>
<div class="abs feature-icon" style="left:78px" role="img" aria-label="Candelabra icon"></div>
<div class="abs feature-icon" style="left:433px" role="img" aria-label="Decorated candle icon"></div>
<div class="abs feature-icon" style="left:788px" role="img" aria-label="Candle holder icon"></div>

<section class="welcome">
  <div class="abs welcome-photo" role="img" aria-label="Group of white pillar candles"></div>
  <i class="abs welcome-mark"></i>
  <h2 class="abs welcome-title">WELCOME TO HIRE <span class="accent">A LANTERN</span></h2>
  <p class="abs welcome-text">We are a family owned and operated company and began making decorative candles for all occasions. &nbsp;All of our candles are individually hand made in our candle studio, situated in Kettleby, outside Harbourton. &nbsp;Our wax is local and of a very high quality, and dripless! Our wax is also made with a high melting point, which means it will not melt or bend in hot temperatures.</p>
  <div class="abs btn-dark welcome-btn">Read More</div>
</section>

<section class="abs event event-wedding" role="img" aria-label="Wedding reception hall lit with fairy lights and pillar candles">
  <div class="event-icon" role="img" aria-label="Wedding couple icon"></div>
  <h3 class="event-title">WEDDINGS EVENTS</h3>
  <p class="event-text">Lorem ipsum dolor sit amet, consectetuer adipiscing elit, sed diam nonummy nibh euismod tincidunt ut at volutpat. Ut wisi enim ad minim veniam.</p>
  <div class="event-btn">Read More</div>
</section>
<section class="abs event event-corporate" role="img" aria-label="Corporate dinner venue with candle centrepieces">
  <div class="event-icon" role="img" aria-label="Presenter and audience icon"></div>
  <h3 class="event-title">CORPORATE EVENTS</h3>
  <p class="event-text">Lorem ipsum dolor sit amet, consectetuer adipiscing elit, sed diam nonummy nibh euismod tincidunt ut at volutpat. Ut wisi enim ad minim veniam.</p>
  <div class="event-btn">Read More</div>
</section>

<section class="testimonials">
  <h2 class="abs testimonial-title">WHAT OUR <span class="accent">CLIENTS SAY ABOUT US</span></h2>
  <div class="abs testimonial-rule"></div>
  <div class="abs client-photo" role="img" aria-label="Client portrait"></div>
  <svg class="abs quote-badge" viewBox="0 0 36 36"><circle cx="18" cy="18" r="18" fill="#0b0b0b"/><text x="18" y="29" text-anchor="middle" font-size="26" font-family="Georgia,serif" fill="#fff">“</text></svg>
  <p class="abs testimonial-text">Lorem ipsum dolor sit amet, consectetuer adipiscing elit, sed diam nonummy nibh euismod tincidunt ut laoreet dolore magna aliquam erat volutpat. Ut wisi enim ad minim veniam, quis nostrud exerci tation ullamcorper suscipit lobortis nisl ut aliquip ex ea commodo consequat. Duis autem vel eum iriure dolor in hendrerit in vulputate velit esse molestie consequat, vel illum dolore eu feugiat nulla facilisis at vero eros et accumsan et iusto odio dignissim.</p>
  <div class="abs client-name">Mara T. Ellison</div>
  <div class="abs slider-dots"><i></i><i></i><i></i><i></i></div>
</section>

<section class="abs lower"></section>
<h2 class="abs section-title decor-title">OTHER <span class="accent">DECOR HIRES</span></h2>
<div class="abs decor-rule"></div>
<p class="abs decor-intro">We would also like to include a section for hiring out decor such as:</p>
<ul class="abs decor-list">
  <li>Glass Vases</li>
  <li>Candle Bras</li>
  <li>Overlays And Chairs Sachets</li>
  <li>Chair Covers</li>
</ul>
<div class="abs decor-photo" role="img" aria-label="Lit white pillar candle"></div>

<h2 class="abs section-title inquiry-title">QUICK <span class="accent">INQUIRY</span></h2>
<div class="abs inquiry-rule"></div>
<div class="abs field" style="top:1837px;height:40px">Name</div>
<div class="abs field" style="top:1885px;height:40px">Email</div>
<div class="abs field" style="top:1934px;height:69px">Message</div>
<div class="abs btn-dark submit">Submit</div>

<nav class="abs footer-nav"></nav>
<div class="abs footer-links">HOME<span>|</span>ABOUT US<span>|</span>OUR PRODUCTS<span>|</span>TESTIMONIALS<span>|</span>CONTACT US</div>
<i class="abs social" style="left:997px"></i>
<i class="abs social" style="left:1041px"></i>
<i class="abs social" style="left:1086px"></i>

<footer class="abs footer"></footer>
<div class="abs footer-item" style="left:83px">
  <span class="footer-pin"><svg width="14" height="18" viewBox="0 0 14 18"><path d="M7 0a7 7 0 0 0-7 7c0 5 7 11 7 11s7-6 7-11a7 7 0 0 0-7-7z" fill="#fff"/><circle cx="7" cy="7" r="2.5" fill="#f7850f"/></svg></span>
  <div style="color:#fff"><b>Hire A Lantern</b>123, Lorewam Dollar, Smit Amet - 123456</div>
</div>
<div class="abs footer-item" style="left:412px">
  <span class="footer-pin"><svg width="15" height="15" viewBox="0 0 24 24"><path d="M6.6 10.8a15 15 0 0 0 6.6 6.6l2.2-2.2c.3-.3.7-.4 1-.2 1.1.4 2.3.6 3.6.6.6 0 1 .4 1 1V20c0 .6-.4 1-1 1A17 17 0 0 1 3 4c0-.6.4-1 1-1h3.5c.6 0 1 .4 1 1 0 1.3.2 2.5.6 3.6.1.3 0 .7-.2 1z" fill="#fff"/></svg></span>
  <div style="color:#fff"><b>Call Us :</b>123 456 7890</div>
</div>
<div class="abs footer-item" style="left:590px">
  <span class="footer-pin"><svg width="16" height="11" viewBox="0 0 20 14"><rect width="20" height="14" fill="#fff"/><path d="M0 0 L10 8 L20 0" stroke="#f7850f" stroke-width="1.8" fill="none"/></svg></span>
  <div style="color:#fff"><b>Email Us :</b>info@hirealantern.com</div>
</div>
<div class="abs footer-brand" style="color:#fff"><i></i>HIRE A LANTERN</div>
<div class="abs copyright">Copyright © 2016 Hire A Lantern. &nbsp;All Rights Reserved.</div>

</body>
</html>
```